Emerging Ed-Tech Startup seeking Stationery Designs!

We are in need of basic set of stationery designs to be used for our business operations, letters, emails, and in-office materials. We are a technology startup enhancing on campus work experience offerings by establishing a collaborative work environment for the completion of such tasks.

Our colors are Vibrant Tiffany Blue/Black/White.

Website: www.campusnorthway.com (Still under construction aside from the landing pages)

Please make sure the designs use a brighter more vibrant tiffany blue color than seen in the image files uploaded. We are not using those materials.

Our logo has been added as a file as well, please use that for any designs (include that logo). Thank you.

```html
<!DOCTYPE html>
<html lang="en">
<head>
<meta charset="utf-8">
<title>Campus Northway Stationery</title>
<link rel="stylesheet" href="https://fonts.googleapis.com/css2?family=Jost:wght@400;500;600&family=Arimo:wght@400&display=swap">
<style>
:root{
  --tiffany:#0be8ea;
  --ink:#111111;
  --paper:#ffffff;
  --rule:#222222;
  --backdrop:#9c7750;
  --faint:#eef1f2;
}
*{box-sizing:border-box;margin:0;padding:0}
html,body{width:1200px;height:709px;overflow:hidden}
body{background:var(--backdrop);font-family:"Jost",sans-serif;color:var(--ink);position:relative}
.sheet{position:absolute;background:var(--paper);overflow:hidden;box-shadow:0 1px 3px rgba(0,0,0,.25)}
.band{position:absolute;left:0;right:0;background:var(--tiffany)}
.rule{position:absolute;left:0;right:0;height:1px;background:var(--rule)}
.brand{position:absolute;display:flex;align-items:center;gap:5px;font-weight:600;color:var(--ink);line-height:1;letter-spacing:.5px}
.brand-mark{width:9px;height:9px;background:var(--tiffany);flex:none}
.brand-name{display:flex;flex-direction:column}
.contact{position:absolute;font-size:7px;letter-spacing:.6px;color:var(--ink);white-space:nowrap;display:flex;align-items:center;gap:3px}
.contact svg{width:7px;height:7px}
.ghost-name{position:absolute;font-weight:600;color:var(--faint);line-height:.9;text-align:center}

/* letterhead */
.letterhead{left:35px;top:48px;width:344px;height:447px}
.letterhead .brand{left:130px;top:16px;font-size:15px}
.letterhead .ghost-name{left:0;right:0;top:160px;font-size:52px;color:#e8ecee}
.letterhead .rule{top:410px}
.letterhead .band{top:414px;height:33px}

/* fax */
.fax{left:418px;top:48px;width:345px;height:445px}
.fax .brand{left:25px;top:16px;font-size:15px}
.fax .head-divider{position:absolute;left:238px;top:26px;width:1px;height:22px;background:#999}
.fax .head-contact{left:244px;font-size:6.5px;letter-spacing:.2px}
.fax-title{position:absolute;left:25px;top:95px;font-family:"Arimo",sans-serif;font-size:21px;font-weight:400}
.fax-row{position:absolute;left:29px;width:287px;height:1px;background:var(--rule)}
.fax-label{position:absolute;font-family:"Arimo",sans-serif;font-size:9px}
.fax .rule{top:410px}
.fax .band{top:414px;height:31px}

/* envelopes */
.envelope-small{left:785px;width:385px;height:166px}
.envelope-small .header{position:absolute;left:0;right:0;top:0;height:58px;display:flex;align-items:center;justify-content:center;font-weight:600;font-size:17px;letter-spacing:1px;border-bottom:1px solid var(--rule)}
.env-white{top:46px}
.env-black{top:234px}
.env-black .header{background:var(--ink);color:var(--paper)}
.env-tiffany{top:416px}
.env-tiffany .header{background:var(--tiffany);color:var(--paper);border-bottom:none}

/* card / signature */
.signature{left:30px;top:523px;width:366px;height:100px}
.signature .brand{left:10px;top:10px;font-size:12px}
.person{position:absolute;right:14px;top:14px;text-align:right;line-height:1.35}
.person-name{font-size:10px;font-weight:500;letter-spacing:.3px}
.person-role{font-size:7.5px;letter-spacing:.4px}
.signature .rule{top:62px}
.signature .band{top:67px;height:33px}
.caption{position:absolute;left:128px;top:642px;font-size:19px;color:var(--paper);font-weight:400}

/* envelope large */
.envelope{left:457px;top:519px;width:385px;height:168px}
.envelope .brand{left:14px;top:12px;font-size:15px}
.envelope .address{left:14px;top:65px}
.envelope .ghost-name{right:14px;top:90px;font-size:13px;text-align:right;color:#e6eaec}
.envelope .rule{top:142px}
.envelope .band{top:147px;height:21px}
</style>
</head>
<body>

<svg width="0" height="0" style="position:absolute" aria-hidden="true">
  <symbol id="icon-phone" viewBox="0 0 10 10"><path d="M2 1l2 2-1 1.2a6 6 0 0 0 2.8 2.8L7 6l2 2-1.3 1.3C4.5 9.3.7 5.5.7 2.3z" fill="currentColor"/></symbol>
  <symbol id="icon-globe" viewBox="0 0 10 10"><circle cx="5" cy="5" r="4.3" fill="none" stroke="currentColor" stroke-width="1.2"/><path d="M.8 5h8.4M5 .8c-2.4 2.6-2.4 5.8 0 8.4M5 .8c2.4 2.6 2.4 5.8 0 8.4" fill="none" stroke="currentColor" stroke-width=".8"/></symbol>
  <symbol id="icon-mobile" viewBox="0 0 10 10"><rect x="2.5" y=".5" width="5" height="9" rx="1" fill="currentColor"/><rect x="3.4" y="1.6" width="3.2" height="5.8" fill="#fff"/></symbol>
  <symbol id="icon-home" viewBox="0 0 10 10"><path d="M5 .8L.5 5h1.4v4h2.4V6.5h1.4V9h2.4V5h1.4z" fill="currentColor"/></symbol>
</svg>

<!-- Letterhead -->
<section class="sheet letterhead">
  <div class="brand"><span class="brand-mark"></span><span class="brand-name"><span>CAMPUS</span><span>NORTHWAY</span></span></div>
  <div class="ghost-name">CAMPUS<br>NORTHWAY</div>
  <div class="rule"></div>
  <div class="band"></div>
  <div class="contact" style="left:92px;top:419px"><svg><use href="#icon-phone"/></svg>+91 24 5512408 &nbsp;<svg><use href="#icon-globe"/></svg>www.campusnorthway.com</div>
  <div class="contact" style="left:127px;top:431px">House#B-14 Lake Avenue</div>
</section>

<!-- Fax -->
<section class="sheet fax">
  <div class="brand"><span class="brand-mark"></span><span class="brand-name"><span>CAMPUS</span><span>NORTHWAY</span></span></div>
  <div class="head-divider"></div>
  <div class="contact head-contact" style="top:26px"><svg><use href="#icon-phone"/></svg>+91 24 5512408</div>
  <div class="contact head-contact" style="top:37px"><svg><use href="#icon-globe"/></svg>www.campusnorthway.com</div>
  <h1 class="fax-title">FAX</h1>
  <span class="fax-label" style="left:29px;top:141px">To</span><span class="fax-label" style="left:215px;top:141px">From</span>
  <div class="fax-row" style="top:157px"></div>
  <span class="fax-label" style="left:29px;top:183px">Fax</span><span class="fax-label" style="left:215px;top:183px">Pages</span>
  <div class="fax-row" style="top:197px"></div>
  <span class="fax-label" style="left:29px;top:222px">Phone</span><span class="fax-label" style="left:215px;top:222px">Date</span>
  <div class="fax-row" style="top:238px"></div>
  <span class="fax-label" style="left:29px;top:264px">Re</span><span class="fax-label" style="left:215px;top:264px">CC</span>
  <div class="fax-row" style="top:278px"></div>
  <div class="rule"></div>
  <div class="band"></div>
  <div class="contact" style="left:127px;top:426px">House#B-14 Lake Avenue</div>
</section>

<!-- Small envelopes -->
<section class="sheet envelope-small env-white"><div class="header">CAMPUS NORTHWAY</div></section>
<section class="sheet envelope-small env-black"><div class="header">CAMPUS NORTHWAY</div></section>
<section class="sheet envelope-small env-tiffany"><div class="header">CAMPUS NORTHWAY</div></section>

<!-- Email signature -->
<section class="sheet signature">
  <div class="brand"><span class="brand-mark"></span><span class="brand-name"><span>CAMPUS</span><span>NORTHWAY</span></span></div>
  <div class="person"><div class="person-name">MR. AARON PELL</div><div class="person-role">MARKETING MANAGER</div></div>
  <div class="rule"></div>
  <div class="band"></div>
  <div class="contact" style="left:9px;top:73px;font-size:6.5px"><svg><use href="#icon-phone"/></svg>+91 24 5512408 <svg><use href="#icon-mobile"/></svg>+91 17 4490318 <svg><use href="#icon-globe"/></svg>www.campusnorthway.com</div>
  <div class="contact" style="left:9px;top:88px;font-size:6.5px"><svg><use href="#icon-home"/></svg>House#B-14 Lake Avenue</div>
</section>
<p class="caption">Email Signtaure</p>

<!-- Envelope -->
<section class="sheet envelope">
  <div class="brand"><span class="brand-mark"></span><span class="brand-name"><span>CAMPUS</span><span>NORTHWAY</span></span></div>
  <div class="contact address" style="font-size:6.5px">House#B-14 Lake Avenue</div>
  <div class="ghost-name">CAMPUS<br>NORTHWAY</div>
  <div class="rule"></div>
  <div class="band"></div>
  <div class="contact" style="left:14px;top:154px;font-size:6.5px">www.campusnorthway.com</div>
</section>

</body>
</html>
```